Bootstrap site for Cloud Services company

Hi,

First I'd like you to submit you design of the homepage. If you are the winner, I'll get you do design the rest and code it up in HTML, CSS etc using bootstrap.

Why bootstrap? This will probably mean
that you understand the fundamentals of CSS and know how to
make a good-looking website. Also should mean that you can throw
together this site relatively easily so you can focus on the design
work. I'll need some icons and banner style images done.

There's no server-side coding involved, and there's also no content to write, just put placemarker text wherever appropriate. You must be familiar with bootstrap.

Our business sells Velmora Suite for Business and IT support services.

The icon for our business is attached.

Basically I want you to go by the design of this site
http://lnk.example-short.net/qR7x

However, don't just copy it. I want it to be of a similar layout and
style, but be creative.

I like the simplicity and how it's easy to follow visually.

Just submit the homepage, and if you're successful, I'll get you to
design the rest of the pages for me and code up the pages.

Thanks!

Target Market(s)

We are marketing towards businesses that need their IT managed for them.

Industry/Entity Type

Business

Requirements
Must have
• I like how clean and nice the roboto font is, but it's up to you.

You're welcome to take inspiration from the 'Tarvix Pulse' layout and design. Nice use of white space and layout.

Menu headings at the top are as follows:
Support | Deployment | Training | Development | Contact Us |
About

Home page:

In a similar style of the referenced webpage http://lnk.example-short.net/qR7x, I'd
like a single banner that says "Brisbane's leading Velmora Suite
specialists". In the banner have a computer screen or laptop and a
tablet or smartphone with some 'velmora suite for business' style of
logos coming out of it be creative with some nice design.

Under that, 3 square (or something) icons.
Save Money | Collaborate | Grow
just put some placemarker text in it in a similar fashion to the
reference site.

Just throw some other things in there to fill it up a bit.
Should not have
• http://lnk.example-short.net/qR7x
I don't want the scrolling banner with the site above, static is fine.

I don't like how when the menu is moused-over, the whole page
moves down.

No stock photos of 'successful business people' or 'very attractive
telephone operator waiting to take your call' :)

```html
<!DOCTYPE html>
<html lang="en">
<head>
<meta charset="utf-8">
<title>Nimbrel – Velmora Suite Specialists</title>
<link href="https://fonts.googleapis.com/css2?family=Roboto:wght@400;500;700&family=Roboto+Condensed:wght@400;700&display=swap" rel="stylesheet">
<style>
:root{
  --page:#f2f2f2;
  --header-top:#f4f5f6;
  --header-bottom:#c9cdd1;
  --ink:#222;
  --orange:#f7931e;
  --orange-btn:#f26a10;
  --blue:#1c7fe0;
  --blue-dark:#1f5fae;
  --red:#e8342c;
  --footer:#151515;
  --footer-bar:#232323;
  --field:#333;
  --white:#fff;
}
*{box-sizing:border-box;margin:0;padding:0}
html,body{width:938px;height:1200px;overflow:hidden}
body{background:var(--page);font-family:Roboto,Arial,sans-serif;color:var(--ink);position:relative}
.abs{position:absolute}

/* header */
.site-header{left:0;top:0;width:938px;height:66px;background:linear-gradient(var(--header-top),var(--header-bottom));border-bottom:1px solid #9aa3ab}
.brand{left:69px;top:18px;display:flex;align-items:center;gap:10px;font:700 27px Roboto,sans-serif;color:#1a1a1a}
.brand-dot{width:30px;height:30px;border-radius:50%;background:var(--blue)}
.nav{left:0;top:0;height:66px;width:938px;list-style:none}
.nav li{position:absolute;top:0;height:66px;font:500 9px Roboto,sans-serif;letter-spacing:.2px;text-align:center;padding-top:26px;transform:translateX(-50%);white-space:nowrap}
.nav li svg{display:block;margin:6px auto 0}
.nav li.active{background:var(--white);border-top:2px solid var(--red);width:63px;padding-top:24px}

.search{left:718px;top:83px;width:151px;height:22px;border:1px solid #bbb;border-radius:11px;background:var(--white);font-size:8px;color:#333;display:flex;align-items:center;padding-left:8px;gap:5px;white-space:nowrap}

/* static banner */
.banner-frame{left:196px;top:134px;width:545px;height:306px;background:#e2e2e2;border-radius:4px}
.banner-panel{left:201px;top:138px;width:536px;height:299px;background:var(--white)}
.banner-art{left:260px;top:150px;width:420px;height:250px;background:linear-gradient(#dfe4ea,#b8c2cc);border-radius:6px}
.banner-caption{left:212px;top:410px;font:700 11px Roboto,sans-serif;letter-spacing:.2px;display:flex;align-items:center;gap:10px;white-space:nowrap}
.banner-rule{left:234px;top:468px;width:466px;border-top:1px dashed #aaa}

/* call to action */
.cta{left:326px;top:500px;width:278px;height:58px;background:linear-gradient(#4597ee,#1e6fd6);border-bottom:3px solid var(--blue-dark);text-align:center;color:var(--white)}
.cta-title{font:700 15px "Roboto Condensed",sans-serif;margin-top:12px}
.cta-sub{font:400 9px Roboto,sans-serif;color:#d6e7fb;margin-top:4px}

/* features */
.feature{top:594px;width:252px;height:308px;background:var(--white);border:1px solid #ccc;border-radius:18px;text-align:center}
.feature-icon{position:absolute;left:89px;top:19px;width:74px;height:74px;border-radius:50%;display:flex;align-items:center;justify-content:center}
.feature-title{position:absolute;left:0;width:100%;top:108px;font:400 25px "Roboto Condensed",sans-serif}
.feature-text{position:absolute;left:18px;width:216px;top:143px;font:400 9.2px/14px Arial,sans-serif;color:#333;text-align:justify;text-align-last:center}
.btn{position:absolute;left:86px;top:267px;width:78px;height:28px;border-radius:3px;color:var(--white);font:400 11px Arial,sans-serif;line-height:26px}
.save .feature-title{color:var(--orange)}
.save .feature-icon{background:radial-gradient(circle at 50% 35%,#ffb83a,#f08a00)}
.save .btn{background:linear-gradient(#ff8a3d,var(--orange-btn));border:1px solid #d2560a}
.collab .feature-title{color:var(--blue-dark)}
.collab .feature-icon{background:radial-gradient(circle at 50% 35%,#3fa0ff,#0f63d0)}
.collab .btn{background:linear-gradient(#3ba3ff,#1180ea);border:1px solid #0c69c4}
.grow .feature-title{color:var(--red)}
.grow .feature-icon{background:radial-gradient(circle at 50% 35%,#ff7066,#e12c26)}
.grow .btn{background:linear-gradient(#ff4a3a,#e01a12);border:1px solid #b81410}

/* footer */
.site-footer{left:0;top:941px;width:938px;height:223px;background:var(--footer);color:var(--white)}
.footer-col h2{font:400 19px Roboto,sans-serif}
.post-title{font:700 11.5px Roboto,sans-serif}
.post-text{font:400 8.5px/14px Arial,sans-serif;margin-top:3px;width:250px}
.services{list-style:none;font:400 8px Arial,sans-serif}
.services li{height:18.8px;display:flex;align-items:center;gap:6px;white-space:nowrap}
.services li::before{content:"";width:2px;height:5px;background:var(--white)}
.divider{top:960px;width:1px;height:188px;background:#3a3a3a}
.field{left:622px;width:245px;background:var(--field);font:400 9.5px Arial,sans-serif;padding:5px 10px;color:#eee}
.submit{left:622px;top:1119px;width:78px;height:27px;border-radius:3px;background:linear-gradient(#ff7a2e,var(--orange-btn));border:1px solid #ff9a5a;color:var(--white);font:400 11px Arial,sans-serif;text-align:center;line-height:25px}
.footer-bar{left:0;top:1164px;width:938px;height:36px;background:var(--footer-bar);border-top:1px solid #444;color:var(--white);font:400 8px Arial,sans-serif;padding:13px 0 0 69px}
</style>
</head>
<body>

<header class="site-header abs">
  <div class="brand abs"><span class="brand-dot"></span>Nimbrel</div>
  <ul class="nav abs">
    <li class="active" style="left:427px">SUPPORT<svg width="8" height="5"><path d="M1 1l3 3 3-3" stroke="#333" stroke-width="1.4" fill="none"/></svg></li>
    <li style="left:511px">DEPLOYMENT<svg width="8" height="5"><path d="M1 1l3 3 3-3" stroke="#333" stroke-width="1.4" fill="none"/></svg></li>
    <li style="left:595px">TRAINING<svg width="8" height="5"><path d="M1 1l3 3 3-3" stroke="#333" stroke-width="1.4" fill="none"/></svg></li>
    <li style="left:682px">DEVELOPMENT<svg width="8" height="5"><path d="M1 1l3 3 3-3" stroke="#333" stroke-width="1.4" fill="none"/></svg></li>
    <li style="left:776px">CONTACT US<svg width="8" height="5"><path d="M1 1l3 3 3-3" stroke="#333" stroke-width="1.4" fill="none"/></svg></li>
    <li style="left:852px">ABOUT<svg width="8" height="5"><path d="M1 1l3 3 3-3" stroke="#333" stroke-width="1.4" fill="none"/></svg></li>
  </ul>
</header>

<div class="search abs">
  <svg width="9" height="9"><circle cx="3.7" cy="3.7" r="2.8" stroke="#333" stroke-width="1.2" fill="none"/><path d="M5.8 5.8l2.6 2.6" stroke="#333" stroke-width="1.4"/></svg>
  Enter keyword and press enter
</div>

<div class="banner-frame abs"></div>
<div class="banner-panel abs"></div>
<div class="banner-art abs" role="img" aria-label="Row of five smartphones showing apps, maps and stock charts"></div>
<div class="banner-caption abs">
  <svg width="11" height="7"><ellipse cx="5.5" cy="3.5" rx="5" ry="3" fill="#333"/><circle cx="5.5" cy="3.5" r="1.5" fill="#fff"/></svg>
  BRISBANE'S LEADING VELMORA SUITE SPECIALISTS
</div>
<div class="banner-rule abs"></div>

<a class="cta abs">
  <div class="cta-title">Want to know much more?</div>
  <div class="cta-sub">Find interesting in here then let's get in touch</div>
</a>

<section class="feature save abs" style="left:69px">
  <div class="feature-icon"><svg width="40" height="32"><rect x="2" y="7" width="36" height="24" rx="3" fill="none" stroke="#fff" stroke-width="3"/><path d="M14 7V3h12v4" stroke="#fff" stroke-width="3" fill="none"/><path d="M11 9v20M29 9v20" stroke="#fff" stroke-width="2.5"/></svg></div>
  <h3 class="feature-title">SAVE MONEY</h3>
  <p class="feature-text">Lorem Ipsum is simply dummy text of the printing and typesetting industry. Lorem Ipsum has been the industry's standard dummy text ever since the 1500s, when an unknown printer took a galley of type and scrambled it to make a type specimen book. It has survived not only five centuries, but also the leap into electronic typesetting, remaining essentially unchanged.</p>
  <a class="btn">Read More</a>
</section>
<section class="feature collab abs" style="left:342px">
  <div class="feature-icon"><svg width="40" height="40"><circle cx="17" cy="23" r="13" fill="none" stroke="#fff" stroke-width="2.5"/><path d="M4 23h26M17 10c-7 8-7 18 0 26M17 10c7 8 7 18 0 26" stroke="#fff" stroke-width="2" fill="none"/><circle cx="29" cy="10" r="5" fill="none" stroke="#fff" stroke-width="2.5"/><path d="M29 15v6" stroke="#fff" stroke-width="2.5"/></svg></div>
  <h3 class="feature-title">COLLABORATE</h3>
  <p class="feature-text">Lorem Ipsum is simply dummy text of the printing and typesetting industry. Lorem Ipsum has been the industry's standard dummy text ever since the 1500s, when an unknown printer took a galley of type and scrambled it to make a type specimen book. It has survived not only five centuries, but also the leap into electronic typesetting, remaining essentially unchanged.</p>
  <a class="btn">Read More</a>
</section>
<section class="feature grow abs" style="left:616px">
  <div class="feature-icon"><svg width="40" height="38"><path d="M12 4v22M26 4v22M12 11h14M12 18h14" stroke="#fff" stroke-width="3" fill="none"/><path d="M3 28c4-3 6 3 11 0s7 3 11 0 7 3 12 0M3 35c4-3 6 3 11 0s7 3 11 0 7 3 12 0" stroke="#fff" stroke-width="2.2" fill="none"/></svg></div>
  <h3 class="feature-title">GROW</h3>
  <p class="feature-text">Lorem Ipsum is simply dummy text of the printing and typesetting industry. Lorem Ipsum has been the industry's standard dummy text ever since the 1500s, when an unknown printer took a galley of type and scrambled it to make a type specimen book. It has survived not only five centuries, but also the leap into electronic typesetting, remaining essentially unchanged.</p>
  <a class="btn">Read More</a>
</section>

<footer class="site-footer abs"></footer>
<div class="divider abs" style="left:342px"></div>
<div class="divider abs" style="left:591px"></div>

<div class="footer-col abs" style="left:69px;top:960px;color:#fff">
  <h2>Blog Posts</h2>
  <h4 class="post-title" style="margin-top:24px">Lorem Ipsum is simply dummy</h4>
  <p class="post-text">Text of the printing and typesetting industry. Lorem Ipsum has been the industry's standard dummy text ever since the 1500s, when an unknown printer took a galley of type and scrambled it to make a type specimen book.</p>
  <h4 class="post-title" style="margin-top:8px">Lorem Ipsum is simply dummy</h4>
  <p class="post-text">Text of the printing and typesetting industry. Lorem Ipsum has been the industry's standard dummy text ever.</p>
</div>

<div class="footer-col abs" style="left:367px;top:960px;color:#fff">
  <h2>Services</h2>
  <ul class="services" style="margin-top:21px">
    <li>Lorem Lipsum Dolor Sit Amet</li>
    <li>Lorem Lipsum Dolor Sit Amet</li>
    <li>Lorem Lipsum Dolor Sit Amet</li>
    <li>Lorem Lipsum Dolor Sit Amet</li>
    <li>Lorem Lipsum Dolor Sit Amet</li>
    <li>Lorem Lipsum Dolor Sit Amet</li>
  </ul>
</div>

<div class="footer-col abs" style="left:621px;top:960px;color:#fff"><h2>Signup Today</h2></div>
<div class="field abs" style="top:998px;height:22px">Name</div>
<div class="field abs" style="top:1029px;height:22px">Email</div>
<div class="field abs" style="top:1060px;height:44px">Message</div>
<div class="submit abs">Submit</div>

<div class="footer-bar abs">Copyrights © 2012. All Rights Reserved.</div>

</body>
</html>
```